Request for Business Card Design

Hi. My name is Marlene, I am looking for a new business card design for my company, Quarrow Signal Instruments, LLC. I really like the design you did for Tarsel Venture and was hoping you could do something similar using our full logo and our mark. I am also open to any raised texture design using our mark. I have attached our full logo, which would need to be somewhere on the card, as well as the mark in both outline and full form, as well as our brand colors / guide. The card does not have to be white, as long as our logo and mark appear. I actually like darker colored business cards more, but am open to all options. If you are interested in working with me, please let me know. We would also take the business card design into letterhead design if you can do that.

```html
<!DOCTYPE html>
<html lang="en">
<head>
<meta charset="utf-8">
<title>Quarrow Signal Instruments – Business Card</title>
<link rel="stylesheet" href="https://fonts.googleapis.com/css2?family=Open+Sans:wght@400;600;800&display=swap">
<style>
  :root {
    --backdrop: #232324;
    --card: #3d3d3f;
    --card-deep: #2c2c2e;
    --accent: #1e9cc8;
    --ink-light: #ffffff;
    --ink-muted: #e6e6e6;
  }
  * { box-sizing: border-box; margin: 0; padding: 0; }
  html, body { width: 1200px; height: 780px; overflow: hidden; background: var(--backdrop); }
  body { font-family: "Open Sans", Arial, sans-serif; }

  .canvas { position: relative; width: 1200px; height: 780px; }

  .card {
    position: absolute; top: 70px; width: 370px; height: 640px;
    background: var(--card);
    border-left: 5px solid var(--accent);
    box-shadow: 0 18px 40px rgba(0,0,0,.55);
    overflow: hidden;
  }
  .card--front { left: 170px; }
  .card--back { left: 650px; }

  /* Front: pressed brand name */
  .front-brand {
    position: absolute; left: 50%; top: 50%;
    transform: translate(-50%, -50%) rotate(-90deg);
    display: flex; align-items: center; gap: 22px;
    white-space: nowrap;
  }
  .front-brand__dot { width: 70px; height: 70px; border-radius: 50%; background: var(--card-deep); }
  .front-brand__name {
    font-weight: 800; font-size: 44px; letter-spacing: 3px; color: var(--card-deep);
  }

  /* Back: identity and contacts */
  .brand {
    position: absolute; top: 48px; left: 40px;
    display: flex; align-items: center; gap: 12px;
  }
  .brand__dot { width: 34px; height: 34px; border-radius: 50%; background: var(--accent); }
  .brand__name {
    font-weight: 800; font-size: 17px; letter-spacing: 1.5px; color: var(--ink-light);
    line-height: 1.15;
  }

  .person { position: absolute; left: 40px; top: 330px; }
  .person__name { font-weight: 800; font-size: 40px; color: var(--accent); line-height: 1; }
  .person__role { font-weight: 600; font-size: 17px; color: var(--ink-light); margin-top: 6px; }

  .address {
    position: absolute; left: 40px; top: 420px;
    font-size: 15px; line-height: 1.45; color: var(--ink-muted); font-style: normal;
  }

  .contacts { position: absolute; left: 40px; top: 485px; list-style: none; }
  .contacts li {
    display: flex; align-items: center; gap: 10px;
    font-size: 15px; line-height: 1.6; color: var(--ink-muted);
  }
  .contacts svg { width: 15px; height: 15px; fill: var(--accent); flex: none; }
</style>
</head>
<body>
<main class="canvas">

  <section class="card card--front" aria-label="Card front">
    <div class="front-brand">
      <span class="front-brand__dot"></span>
      <span class="front-brand__name">QUARROW</span>
    </div>
  </section>

  <section class="card card--back" aria-label="Card back">
    <header class="brand">
      <span class="brand__dot"></span>
      <span class="brand__name">QUARROW SIGNAL<br>INSTRUMENTS</span>
    </header>

    <div class="person">
      <p class="person__name">Marlene</p>
      <p class="person__role">Director</p>
    </div>

    <address class="address">
      1180 Harlow Park Drive<br>
      Ferndale, CO 80999
    </address>

    <ul class="contacts">
      <li>
        <svg viewBox="0 0 24 24" aria-hidden="true"><path d="M6.6 10.8a15 15 0 0 0 6.6 6.6l2.2-2.2a1 1 0 0 1 1-.25 11.4 11.4 0 0 0 3.6.57 1 1 0 0 1 1 1V20a1 1 0 0 1-1 1A17 17 0 0 1 3 4a1 1 0 0 1 1-1h3.5a1 1 0 0 1 1 1c0 1.25.2 2.45.57 3.57a1 1 0 0 1-.25 1z"/></svg>
        +001 555 210 4471
      </li>
      <li>
        <svg viewBox="0 0 24 24" aria-hidden="true"><path d="M6 2h10v6H6zM3 9h18v11H3zm3 3v2h2v-2zm4 0v2h2v-2zm4 0v2h2v-2zm-8 4v2h2v-2zm4 0v2h2v-2zm4 0v2h2v-2z"/></svg>
        +001 555 210 4490
      </li>
      <li>
        <svg viewBox="0 0 24 24" aria-hidden="true"><path d="M12 2a10 10 0 1 0 0 20 10 10 0 0 0 0-20zm6.9 6h-3a15 15 0 0 0-1.3-3.9A8 8 0 0 1 18.9 8zM12 4c.8 1.2 1.5 2.5 1.9 4h-3.8c.4-1.5 1.1-2.8 1.9-4zM4.3 14a8 8 0 0 1 0-4h3.4a16 16 0 0 0 0 4zm.8 2h3a15 15 0 0 0 1.3 3.9A8 8 0 0 1 5.1 16zm3-8h-3a8 8 0 0 1 4.3-3.9A15 15 0 0 0 8.1 8zM12 20c-.8-1.2-1.5-2.5-1.9-4h3.8c-.4 1.5-1.1 2.8-1.9 4zm2.3-6H9.7a14 14 0 0 1 0-4h4.6a14 14 0 0 1 0 4zm.3 5.9a15 15 0 0 0 1.3-3.9h3a8 8 0 0 1-4.3 3.9zM16.3 14a16 16 0 0 0 0-4h3.4a8 8 0 0 1 0 4z"/></svg>
        www.quarrowsignal.com
      </li>
      <li>
        <svg viewBox="0 0 24 24" aria-hidden="true"><path d="M2 5h20v14H2zm2 2v.5l8 5 8-5V7zm0 2.8V17h16V9.8l-8 5z"/></svg>
        info@quarrowsignal.com
      </li>
    </ul>
  </section>

</main>
</body>
</html>
```